New Zealand Marlborough Sauvignon Blanc wine packaging design

We need packaging design for our new wine brand, Dunmore Vale. The wine is a New Zealand Marlborough Sauvignon Blanc. We would like the packaging will portray elegance and style with an understated label. We are looking for a label that portrays the elegance of the French Riviera. The label should be round or pill shaped.
Updates

Industry/Entity Type

Wine

Font styles to use
Serif
Sans Serif

Requirements
Must have
• The words in order of importance: Dunmore Vale, Sauvignon Blanc, Marlborough, New Zealand. It should be fit to the bottle posted in the links
Nice to have
• a pill shape or circular shape
Should not have
• Illustrations of wine bottles, wine glasses, or grapes

```html
<!DOCTYPE html>
<html lang="en">
<head>
<meta charset="utf-8">
<title>Dunmore Vale – Marlborough Sauvignon Blanc Labels</title>
<link href="https://fonts.googleapis.com/css2?family=Allura&family=Cormorant+Garamond:wght@500;600&display=swap" rel="stylesheet">
<style>
  :root {
    --backdrop: #f3f3f3;
    --label-paper: #fbfbfa;
    --label-rule: #d8d4cf;
    --ink-grey: #6d6f73;
    --copper: #c4622d;
    --copper-deep: #a9481f;
    --terracotta-light: #e0894b;
    --sea-pale: #a9d6e2;
    --sky-mist: #dbe6ee;
    --riviera-blue: #aec3d9;
    --riviera-blue-deep: #6f93c5;
    --band-blue: #d2e1ec;
    --bloom-pink: #e0308c;
    --leaf-green: #8fb29a;
  }
  html, body {
    margin: 0;
    width: 1200px;
    height: 675px;
    overflow: hidden;
    background: var(--backdrop);
  }
  .label-range {
    width: 1200px;
    height: 675px;
    display: flex;
    align-items: center;
    justify-content: center;
    gap: 90px;
  }
  .wine-label {
    width: 280px;
    height: 420px;
    filter: drop-shadow(0 6px 14px rgba(0,0,0,0.12));
  }
  .label-paper { fill: var(--label-paper); }
  .label-rule { fill: none; stroke: var(--label-rule); stroke-width: 1; }
  .region-text, .country-text {
    font-family: "Cormorant Garamond", serif;
    font-weight: 600;
    font-size: 13px;
    letter-spacing: 2px;
    fill: var(--ink-grey);
  }
  .brand-name {
    font-family: "Allura", cursive;
    font-size: 40px;
  }
  .varietal {
    font-family: "Cormorant Garamond", serif;
    font-weight: 600;
    font-size: 17px;
  }
  .coast .brand-name { fill: var(--copper); }
  .coast .varietal { fill: #fff; }
  .palms .brand-name { fill: var(--copper); font-size: 38px; }
  .palms .varietal { fill: #f2f6fb; }
  .bloom .brand-name { fill: var(--copper); }
  .bloom .varietal { fill: var(--ink-grey); }
</style>
</head>
<body>
<main class="label-range">

  <!-- Coastline edition -->
  <svg class="wine-label coast" viewBox="0 0 260 390" aria-label="Dunmore Vale Sauvignon Blanc label, coastline edition">
    <defs>
      <linearGradient id="coast-band" x1="0" y1="0" x2="1" y2="0">
        <stop offset="0" stop-color="var(--terracotta-light)"/>
        <stop offset="1" stop-color="var(--copper-deep)"/>
      </linearGradient>
      <linearGradient id="coast-scene" x1="0" y1="0" x2="1" y2="1">
        <stop offset="0.35" stop-color="var(--copper)"/>
        <stop offset="0.55" stop-color="var(--sea-pale)"/>
        <stop offset="1" stop-color="var(--sky-mist)"/>
      </linearGradient>
      <path id="coast-top-arc" d="M35 130 A95 95 0 0 1 225 130"/>
      <path id="coast-bottom-arc" d="M35 270 A95 95 0 0 0 225 270"/>
    </defs>
    <rect class="label-paper" x="2" y="2" width="256" height="386" rx="122"/>
    <rect class="label-rule" x="10" y="10" width="240" height="370" rx="114"/>
    <text class="region-text"><textPath href="#coast-top-arc" startOffset="50%" text-anchor="middle">MARLBOROUGH</textPath></text>
    <path role="img" aria-label="Illustration of terracotta coastal cliffs above a pale blue sea" fill="url(#coast-scene)" d="M45 212 V150 A85 85 0 0 1 215 150 V212 Q170 200 130 212 T45 212 Z"/>
    <text class="brand-name" x="130" y="243" text-anchor="middle">Dunmore Vale</text>
    <path fill="var(--sky-mist)" d="M45 262 Q90 252 130 260 T215 258 V266 H45 Z"/>
    <path fill="url(#coast-band)" d="M45 266 Q90 258 130 266 T215 264 V302 Q210 308 200 308 H60 Q48 306 45 300 Z"/>
    <text class="varietal" x="130" y="292" text-anchor="middle">Sauvignon Blanc</text>
    <text class="country-text"><textPath href="#coast-bottom-arc" startOffset="50%" text-anchor="middle">NEW ZEALAND</textPath></text>
  </svg>

  <!-- Palm edition -->
  <svg class="wine-label palms" viewBox="0 0 260 390" aria-label="Dunmore Vale Sauvignon Blanc label, palm edition">
    <defs>
      <linearGradient id="palms-band" x1="0" y1="0" x2="0" y2="1">
        <stop offset="0" stop-color="var(--riviera-blue)"/>
        <stop offset="1" stop-color="var(--riviera-blue-deep)"/>
      </linearGradient>
      <path id="palms-top-arc" d="M35 130 A95 95 0 0 1 225 130"/>
      <path id="palms-bottom-arc" d="M35 270 A95 95 0 0 0 225 270"/>
    </defs>
    <rect class="label-paper" x="2" y="2" width="256" height="386" rx="122"/>
    <rect class="label-rule" x="10" y="10" width="240" height="370" rx="114"/>
    <text class="region-text"><textPath href="#palms-top-arc" startOffset="50%" text-anchor="middle">MARLBOROUGH</textPath></text>
    <path role="img" aria-label="Illustration of white palm trees against a pale blue Riviera sky" fill="var(--riviera-blue)" d="M45 222 V150 A85 85 0 0 1 215 150 V222 Z"/>
    <text class="brand-name" x="130" y="255" text-anchor="middle">Dunmore Vale</text>
    <path fill="url(#palms-band)" d="M45 266 Q90 258 130 266 T215 264 V300 H45 Z"/>
    <text class="varietal" x="130" y="288" text-anchor="middle">Sauvignon Blanc</text>
    <text class="country-text"><textPath href="#palms-bottom-arc" startOffset="50%" text-anchor="middle">NEW ZEALAND</textPath></text>
  </svg>

  <!-- Bloom edition -->
  <svg class="wine-label bloom" viewBox="0 0 260 390" aria-label="Dunmore Vale Sauvignon Blanc label, bloom edition">
    <defs>
      <linearGradient id="bloom-scene" x1="0" y1="0" x2="0" y2="1">
        <stop offset="0" stop-color="var(--sky-mist)"/>
        <stop offset="0.35" stop-color="var(--leaf-green)"/>
        <stop offset="0.6" stop-color="var(--bloom-pink)"/>
        <stop offset="1" stop-color="var(--bloom-pink)"/>
      </linearGradient>
      <path id="bloom-top-arc" d="M35 130 A95 95 0 0 1 225 130"/>
      <path id="bloom-bottom-arc" d="M35 270 A95 95 0 0 0 225 270"/>
    </defs>
    <rect class="label-paper" x="2" y="2" width="256" height="386" rx="122"/>
    <rect class="label-rule" x="7" y="7" width="246" height="376" rx="117"/>
    <rect class="label-rule" x="11" y="11" width="238" height="368" rx="113"/>
    <text class="region-text"><textPath href="#bloom-top-arc" startOffset="50%" text-anchor="middle">MARLBOROUGH</textPath></text>
    <path role="img" aria-label="Illustration of pink bougainvillea blossoms with green leaves" fill="url(#bloom-scene)" d="M45 212 V150 A85 85 0 0 1 215 150 V212 Q170 204 130 212 T45 212 Z"/>
    <text class="brand-name" x="130" y="243" text-anchor="middle">Dunmore Vale</text>
    <path fill="var(--band-blue)" d="M45 256 Q90 248 130 256 T215 254 V306 Q200 312 130 312 Q60 312 45 306 Z"/>
    <text class="varietal" x="130" y="286" text-anchor="middle">Sauvignon Blanc</text>
    <text class="country-text"><textPath href="#bloom-bottom-arc" startOffset="50%" text-anchor="middle">NEW ZEALAND</textPath></text>
  </svg>

</main>
</body>
</html>
```